Business card for law firm

Need business card for new law firm. Think confident, authoritative, conservative, but not stuffy or old-fashioned.

Contact Information for Business Card

Content for card - logo (uploaded), plus the following:

Paul Whitcombe (larger font)
Managing Partner (larger font, but not as large as name)
Level 9, 7 Ferris Lane
Sydney NSW 2000
Main Tel 02 9364 2710
Direct Tel 02 8472 3159
Email paul@qvlegal.com.au
www.qvlegal.com.au

Letterhead design should include logo plus:
Level 9, 7 Ferris Lane
Sydney NSW 2000
Tel 02 8472 3159
www.qvlegal.com.au

```html
<!DOCTYPE html>
<html lang="en">
<head>
<meta charset="utf-8">
<title>Quayvale Legal — Business Card</title>
<link rel="stylesheet" href="https://fonts.googleapis.com/css2?family=Arimo:wght@400;700&display=swap">
<style>
  :root {
    --backdrop: #2b2b2d;
    --card: #f7f7f8;
    --navy: #1b2a5c;
    --ink: #1d1d1f;
    --rule: #3a3a3a;
    --white: #ffffff;
  }
  html, body {
    margin: 0;
    width: 1200px;
    height: 997px;
    overflow: hidden;
    background: var(--backdrop);
    font-family: "Arimo", Arial, sans-serif;
  }
  .canvas {
    position: relative;
    width: 1200px;
    height: 997px;
  }
  .card {
    position: absolute;
    top: 340px;
    width: 500px;
    height: 300px;
    background: var(--card);
    box-shadow: 0 10px 30px rgba(0,0,0,.45);
    overflow: hidden;
  }
  .card--front { left: 70px; }
  .card--back { left: 630px; }

  /* Firm name block */
  .firm-name {
    color: var(--navy);
    font-weight: 400;
    text-transform: uppercase;
    line-height: 1;
  }
  .firm-name__main { display: block; font-size: 44px; letter-spacing: 2px; }
  .firm-name__sub { display: block; font-size: 15px; letter-spacing: 14px; margin-top: 8px; }

  .card--front .brand {
    position: absolute;
    left: 0; right: 0; top: 92px;
    display: flex;
    flex-direction: column;
    align-items: center;
    gap: 18px;
  }
  .brand__square {
    width: 54px; height: 54px;
    background: var(--navy);
  }
  .card--front .firm-name { text-align: center; }

  /* Back */
  .card--back .brand {
    position: absolute;
    left: 36px; top: 52px;
    display: flex;
    align-items: center;
    gap: 12px;
  }
  .card--back .brand__square { width: 40px; height: 40px; }
  .card--back .firm-name__main { font-size: 30px; letter-spacing: 1px; }
  .card--back .firm-name__sub { font-size: 11px; letter-spacing: 9px; margin-top: 5px; }

  .header-rule {
    position: absolute;
    left: 300px; right: 28px; top: 78px;
    height: 1px;
    background: var(--rule);
  }

  .person {
    position: absolute;
    left: 36px; top: 152px;
    right: 28px;
  }
  .person__name-row {
    display: flex;
    align-items: center;
    gap: 8px;
  }
  .person__name {
    color: var(--navy);
    font-weight: 700;
    font-size: 15px;
    text-transform: uppercase;
    white-space: nowrap;
  }
  .person__rule { flex: 1; height: 1px; background: var(--rule); }
  .person__title { font-size: 12px; color: var(--ink); margin-top: 2px; }

  .contact-list {
    position: absolute;
    left: 36px; top: 200px;
    margin: 0; padding: 0;
    list-style: none;
  }
  .contact-list li {
    display: flex;
    align-items: center;
    gap: 12px;
    font-size: 12.5px;
    color: var(--ink);
    height: 20px;
  }
  .contact-icon {
    width: 14px; height: 14px;
    border-radius: 50%;
    background: var(--navy);
    display: flex; align-items: center; justify-content: center;
  }
  .contact-icon svg { width: 9px; height: 9px; fill: var(--white); }

  .address {
    position: absolute;
    right: 28px; top: 172px;
    text-align: right;
    font-size: 11.5px;
    line-height: 1.35;
    color: var(--ink);
  }

  .band { position: absolute; left: 0; bottom: 0; width: 500px; height: 90px; }
  .website {
    position: absolute;
    right: 28px; bottom: 46px;
    color: var(--white);
    font-size: 12px;
    font-weight: 700;
    letter-spacing: 2.5px;
    white-space: nowrap;
  }
</style>
</head>
<body>
<main class="canvas">

  <section class="card card--front" aria-label="Card front">
    <div class="brand">
      <span class="brand__square"></span>
      <div class="firm-name">
        <span class="firm-name__main">Quayvale</span>
        <span class="firm-name__sub">Legal</span>
      </div>
    </div>
  </section>

  <section class="card card--back" aria-label="Card back">
    <div class="brand">
      <span class="brand__square"></span>
      <div class="firm-name">
        <span class="firm-name__main">Quayvale</span>
        <span class="firm-name__sub">Legal</span>
      </div>
    </div>
    <div class="header-rule"></div>

    <div class="person">
      <div class="person__name-row">
        <span class="person__name">Paul Whitcombe</span>
        <span class="person__rule"></span>
      </div>
      <div class="person__title">Managing Partner</div>
    </div>

    <div class="address">
      Level 9, 7 Ferris Lane<br>
      Sydney NSW 2000
    </div>

    <ul class="contact-list">
      <li>
        <span class="contact-icon"><svg viewBox="0 0 10 10"><path d="M1 3c0-1 1-2 2-2h4c1 0 2 1 2 2v1H7V3H3v1H1z M2 5h6l1 4H1z"/></svg></span>
        02 9364 2710
      </li>
      <li>
        <span class="contact-icon"><svg viewBox="0 0 10 10"><path d="M3 0h4c.6 0 1 .4 1 1v8c0 .6-.4 1-1 1H3c-.6 0-1-.4-1-1V1c0-.6.4-1 1-1zm0 1.5v6h4v-6z"/></svg></span>
        02 8472 3159
      </li>
      <li>
        <span class="contact-icon"><svg viewBox="0 0 10 10"><path d="M0 2h10v6H0z M.8 2.6v.4L5 5.8 9.2 3v-.4z" fill-rule="evenodd"/></svg></span>
        paul@qvlegal.com.au
      </li>
    </ul>

    <svg class="band" viewBox="0 0 500 90" preserveAspectRatio="none" aria-hidden="true">
      <path d="M0 82 H206 C240 82 244 22 278 22 H500 V90 H0 Z" fill="var(--navy)"/>
      <path d="M0 70 H192 C222 70 226 22 256 16" fill="none" stroke="var(--ink)" stroke-width="6"/>
    </svg>
    <div class="website">www.qvlegal.com.au</div>
  </section>

</main>
</body>
</html>
```